New web design for a service provider in the medical field

We are looking for a new design for our website. We are a company that repairs and sells medical endoscopes. Our customers include doctors and hospitals. Our current website can be found at https://lumavex.de/en/lumavex-english.
We need a new web design (without programming) for the following 3 pages:
-Startpage https://lumavex.de/en/lumavex-english/
-Used endoscopes https://lumavex.de/en/used-endoscopes/
-Purchase https://lumavex.de/en/purchase/
The design should be modern and stylish.
The blue color of the logo should be reflected on the page, but not too intrusive.
I have uploaded the images from the header. If more images are needed, let me know and I will upload them.

Target Market(s)
Doctors and hospitals

```html
<!DOCTYPE html>
<html lang="en">
<head>
<meta charset="utf-8">
<title>Lumavex – Endoscope Repair &amp; Sale</title>
<link href="https://fonts.googleapis.com/css2?family=Jost:wght@400;500;600;700&display=swap" rel="stylesheet">
<style>
:root{
  --blue:#2b9fe0;
  --blue-light:#4fb3ea;
  --navy:#1d3448;
  --navy-deep:#15293a;
  --ink:#1f2d3a;
  --text:#4a5866;
  --pale:#eef3f8;
  --line:#d9e2ea;
  --white:#ffffff;
}
*{margin:0;padding:0;box-sizing:border-box}
html,body{width:1200px;height:4902px;overflow:hidden}
body{font-family:"Jost",sans-serif;color:var(--text);background:var(--white);position:relative}
.abs{position:absolute}
a{color:inherit;text-decoration:none}

/* header */
.topbar{left:0;top:0;width:1200px;height:40px}
.topbar-info{right:100px;top:10px;display:flex;gap:28px;color:var(--white);font-size:11px;font-weight:600}
.topbar-info span{display:flex;align-items:center;gap:6px}
.brand{display:flex;align-items:center;gap:10px;font-weight:600;color:var(--navy);font-size:24px}
.brand-dot{width:16px;height:16px;border-radius:50%;background:var(--blue)}
.header-brand{left:100px;top:36px}
.nav{left:305px;top:66px;display:flex;gap:30px;font-size:11.5px;font-weight:600;color:var(--ink);letter-spacing:.2px}
.nav a{padding-bottom:8px}
.nav a.active{border-bottom:2px solid var(--blue)}

/* hero */
.hero{left:0;top:110px;width:1200px;height:622px;background:linear-gradient(90deg,#f3f6f9 0%,#e9eef3 100%)}
.hero-photo{left:470px;top:110px;width:730px;height:560px;background:linear-gradient(120deg,#e5eaef 0%,#cfd7df 55%,#f4f6f8 100%)}
.hero-kicker{left:103px;top:278px;color:var(--blue);font-size:21px;font-weight:500}
.hero-title{left:103px;top:304px;color:var(--ink);font-size:40px;font-weight:700;line-height:46px}
.btn{display:inline-flex;align-items:center;justify-content:center;border-radius:30px;font-weight:600;font-size:12.5px;letter-spacing:.3px;color:var(--white)}
.btn-blue{background:var(--blue)}
.btn-navy{background:var(--navy)}
.hero-btn{left:103px;top:421px;width:166px;height:44px;border-radius:4px 22px 22px 22px}
.arrow-dot{width:76px;height:76px;border-radius:50%;background:var(--white);border:2px solid var(--blue);display:flex;align-items:center;justify-content:center}

/* headings */
.section-title{left:0;width:1200px;text-align:center;font-size:33px;font-weight:700;color:var(--ink);letter-spacing:.3px}
.section-title em{font-style:normal;color:var(--blue)}
.title-bar{width:70px;height:3px;background:var(--blue)}
.lead{left:240px;width:720px;text-align:center;font-size:18px;line-height:32px;color:var(--text)}

/* service intro */
.hex{clip-path:polygon(25% 0,75% 0,100% 50%,75% 100%,25% 100%,0 50%)}
.hex-frame{background:var(--blue)}
.intro-img{background:linear-gradient(135deg,#f2f4f6,#cfd5db 60%,#eef1f4)}
.intro-head{left:606px;top:1026px;width:500px;font-size:24px;font-weight:500;line-height:35px;color:var(--ink)}
.intro-copy{left:610px;top:1148px;width:460px;font-size:13.5px;line-height:23px;color:var(--text)}
.intro-copy p+p{margin-top:12px}

/* repair & sale */
.dark-band{left:0;top:1493px;width:1200px;height:420px;background:linear-gradient(180deg,var(--navy) 0%,#243f56 100%)}
.light-band{left:0;top:1913px;width:1200px;height:620px;background:linear-gradient(180deg,#eef3f8 0%,#dfe8f0 100%)}
.dark-title{left:0;width:1200px;text-align:center;color:var(--white);font-size:34px;font-weight:700}
.dark-lead{left:250px;width:700px;text-align:center;color:#e3ebf2;font-size:15.5px;line-height:23px}
.card{text-align:center;color:var(--white);display:flex;flex-direction:column;align-items:center}
.card-blue{background:linear-gradient(135deg,#4ab0ec,#2694d6)}
.card-dark{background:linear-gradient(180deg,#3c566d,#2b4358);border-radius:4px}
.card h3{font-size:19px;font-weight:600;letter-spacing:.4px}
.card .sub{font-size:14.5px}
.card p{font-size:9.5px;line-height:14px;margin-top:6px}
.card .btn{margin-top:14px;width:122px;height:32px;font-size:10px}

/* faulty */
.faulty-title{left:143px;top:2144px;font-size:32px;font-weight:700;color:var(--ink)}
.faulty-title em{font-style:normal;color:var(--blue)}
.faulty-sub{left:143px;top:2210px;font-size:24px;color:var(--ink)}
.faulty-copy{left:143px;top:2252px;width:430px;font-size:15px;line-height:25px;color:var(--text)}
.faulty-btn{left:145px;top:2368px;width:165px;height:42px;font-size:12px}
.scopes-img{background:linear-gradient(135deg,#f3f5f7,#dbe1e7 50%,#f6f8fa)}

/* features */
.feature{padding:40px 40px 0 40px;color:var(--text)}
.feature h4{font-size:17.5px;font-weight:600;color:var(--ink);line-height:20px;margin:14px 0 10px}
.feature p{font-size:13.5px;line-height:19px}
.feature-hl{background:linear-gradient(135deg,#3eaaea,#2390d5);color:var(--white)}
.feature-hl h4,.feature-hl p{color:var(--white)}
.feature svg{display:block}

/* decision */
.decision{left:0;top:3329px;width:1200px;height:660px;background:var(--navy)}
.dec-title{left:0;top:3392px;width:1200px;text-align:center;color:var(--white);font-size:26px;font-weight:700;line-height:32px}
.dec-item{color:var(--white);font-size:9.5px;line-height:14px;color:#d6e0e9}
.dec-item b{display:block;font-size:13px;color:var(--white);font-weight:600;margin-bottom:3px}
.dec-left{text-align:right}
.dec-icon{width:58px;height:58px;border-radius:50%;border:2px solid #e9f1f7;display:flex;align-items:center;justify-content:center}
.dec-core{left:468px;top:3538px;width:266px;height:266px;border-radius:50%;background:radial-gradient(circle,#ffffff 60%,#e7eef5 100%);display:flex;align-items:center;justify-content:center}
.dec-btn{left:476px;top:3882px;width:276px;height:44px;font-size:13px}

/* help */
.help{left:0;top:3989px;width:1200px;height:520px;background:linear-gradient(180deg,#eef3f8,#e4ebf2)}
.field{background:var(--white);border:1px solid #c9d4de;display:flex;align-items:center;gap:10px;padding:0 16px;font-size:12.5px;font-weight:600;color:var(--ink)}
.submit{left:521px;top:4400px;width:162px;height:44px;font-size:13px}

/* footer */
.footer-col h5{font-size:14px;font-weight:600;color:var(--ink);margin-bottom:18px;letter-spacing:.3px}
.footer-col li{list-style:none;font-size:13.5px;color:var(--text);margin-bottom:12px}
.footer-col{border-left:2px solid var(--blue);padding-left:20px}
.social{display:flex;gap:8px}
.social span{width:28px;height:28px;border-radius:50%;background:var(--navy)}
.copyright{left:0;top:4854px;width:1200px;text-align:center;font-size:12px;color:var(--text)}
.copy-line{left:0;top:4835px;width:1200px;height:1px;background:var(--line)}
</style>
</head>
<body>

<!-- header -->
<svg class="abs topbar" viewBox="0 0 1200 40" width="1200" height="40" aria-hidden="true">
  <polygon points="700,0 1200,0 1200,40 680,40" fill="var(--blue)"/>
</svg>
<div class="abs topbar-info">
  <span><svg width="14" height="14" viewBox="0 0 14 14"><circle cx="7" cy="7" r="7" fill="#fff"/><rect x="3.5" y="4.5" width="7" height="5" fill="none" stroke="#2b9fe0"/></svg>info@lumavex.de</span>
  <span><svg width="14" height="14" viewBox="0 0 14 14"><circle cx="7" cy="7" r="7" fill="#fff"/><path d="M4.5 4 l2 0 0 2 -1 1 q1 2 2 2 l1-1 2 0 0 2 q-5 0 -6-6z" fill="#2b9fe0"/></svg>+49 4000 555 123-0</span>
  <span>ENG ▾</span>
</div>
<div class="abs header-brand brand"><span class="brand-dot"></span>Lumavex</div>
<nav class="abs nav">
  <a class="active" href="#">ENDOSCOPE REPAIR</a>
  <a href="#">ENDOSCOPY SYSTEMS</a>
  <a href="#">ENDOSCOPY ACCESSORIES ▾</a>
  <a href="#">ACCESSORIES CATALOG</a>
  <a href="#">PURCHASE</a>
</nav>

<!-- hero -->
<div class="abs hero"></div>
<div class="abs hero-photo" role="img" aria-label="Close-up photo of a flexible endoscope control body on a white stand"></div>
<div class="abs hero-kicker">WELCOME TO LUMAVEX</div>
<h1 class="abs hero-title">PUT YOUR ENDOSCOPE<br>IN RELIABLE HANDS!</h1>
<a class="abs btn btn-blue hero-btn" href="#">LEARN MORE</a>
<svg class="abs" style="left:0;top:620px" width="1200" height="112" viewBox="0 0 1200 112" aria-hidden="true">
  <polygon points="0,4 600,84 600,112 0,112" fill="var(--blue)"/>
  <polygon points="1200,4 600,84 600,112 1200,112" fill="var(--navy)"/>
  <polygon points="0,112 600,84 1200,112" fill="#fff"/>
</svg>
<div class="abs arrow-dot" style="left:565px;top:648px"><svg width="24" height="28" viewBox="0 0 24 28"><path d="M12 2v22M4 16l8 8 8-8" fill="none" stroke="var(--blue)" stroke-width="2"/></svg></div>

<!-- service intro -->
<h2 class="abs section-title" style="top:770px">YOUR FUTURE <em>OUR SERVICE</em></h2>
<div class="abs title-bar" style="left:565px;top:820px"></div>
<p class="abs lead" style="top:842px">Lumavex GmbH is specialised in the repair and sale of Orvana, Pelix and Fuyon flexible medical endoscopes. As a service-oriented company, we are at your side with our knowledge and skills!</p>

<div class="abs hex hex-frame" style="left:99px;top:989px;width:480px;height:416px"></div>
<div class="abs hex intro-img" style="left:103px;top:993px;width:472px;height:408px" role="img" aria-label="Photo of an endoscope handpiece with its insertion tube on a white surface"></div>
<h3 class="abs intro-head">Endoscope repairs and second hand endoscopes from Lumavex cause the outcome matters!</h3>
<div class="abs intro-copy">
  <p>Lumavex is a privileged partner for the start-up facility or optimisation of existing healthcare facilities, doctor's offices and hospitals. The quality and reliability of our products and our offered service are our best advertisement!</p>
  <p>As a result of optimised processes and highly qualified specialists in our company, we can work very quickly and with high quality for your benefit of least possible restrictions in your doctor's office or in your hospital.</p>
</div>

<!-- repair & sale -->
<div class="abs dark-band"></div>
<div class="abs light-band"></div>
<h2 class="abs dark-title" style="top:1560px">REPAIR &amp; SALE ENDOSCOPE</h2>
<p class="abs dark-lead" style="top:1622px">Lorem ipsum dolor sit amet, consectetur adipiscing elit, sed do eiusmod tempor incididunt ut labore et dolore magna aliqua. Ut enim ad minim veniam</p>

<div class="abs card card-blue" style="left:140px;top:1759px;width:302px;height:232px;padding-top:44px">
  <svg width="64" height="40" viewBox="0 0 64 40"><circle cx="18" cy="20" r="14" fill="none" stroke="#fff" stroke-width="2"/><circle cx="18" cy="20" r="8" fill="none" stroke="#fff" stroke-width="2"/><path d="M30 12h26M46 8h14v8h-14z" fill="none" stroke="#fff" stroke-width="2"/></svg>
  <h3 style="margin-top:12px">REPAIR</h3>
  <div class="sub">Endoscope repair service</div>
  <p>Manufacturer-independent we repair and maintain<br>endoscopes, individual components</p>
</div>
<div class="abs card card-dark" style="left:440px;top:1733px;width:337px;height:272px;padding-top:28px">
  <svg width="48" height="48" viewBox="0 0 48 48"><rect x="10" y="6" width="14" height="20" rx="3" fill="none" stroke="#fff" stroke-width="2"/><path d="M17 26v8q0 8 10 8t10-10-8-12" fill="none" stroke="#fff" stroke-width="2"/></svg>
  <h3 style="margin-top:6px">SALE</h3>
  <div class="sub">Used endoscopes</div>
  <p>Our regular stock includes refurbished gastroscopes,<br>colonoscopes, bronchoscopes, cystoscopes and duo-<br>denoscopes from the well-known manufacturers<br>Orvana, Pelix and Fuyon.</p>
  <a class="btn btn-blue" href="#">LEARN MORE</a>
</div>
<div class="abs card card-blue" style="left:777px;top:1759px;width:310px;height:232px;padding-top:28px">
  <svg width="44" height="52" viewBox="0 0 44 52"><rect x="12" y="4" width="18" height="22" rx="3" fill="none" stroke="#fff" stroke-width="2"/><path d="M21 26v18M15 44h12" stroke="#fff" stroke-width="2" fill="none"/></svg>
  <h3 style="margin-top:6px">PURCHASE</h3>
  <div class="sub">Used endoscopes</div>
  <p>We are very interested in buying your old endoscopes –<br>even defective and dismantled! We offer fair condi-<br>tions! Please contact us for a purchase offer!</p>
</div>

<!-- faulty -->
<h2 class="abs faulty-title">FAULTY <em>ENDOSCOPE?</em></h2>
<div class="abs faulty-sub">We ensure quick and smooth repairs!</div>
<p class="abs faulty-copy">Lorem ipsum dolor sit amet, consectetur adipiscing elit, sed do eiusmod tempor incididunt ut labore et dolore magna aliqua. Ut enim ad minim veniam, quis nostrud exercitation ullamco laboris n</p>
<a class="abs btn btn-navy faulty-btn" href="#">PICK UP ORDER</a>
<div class="abs hex hex-frame" style="left:624px;top:2064px;width:476px;height:412px"></div>
<div class="abs hex scopes-img" style="left:628px;top:2068px;width:468px;height:404px" role="img" aria-label="Photo of five endoscope handpieces lying side by side"></div>

<svg class="abs" style="left:0;top:2518px" width="1200" height="104" viewBox="0 0 1200 104" aria-hidden="true">
  <polygon points="0,0 620,62 620,104 0,104" fill="var(--blue)"/>
  <polygon points="1200,0 620,62 620,104 1200,104" fill="var(--navy)"/>
  <polygon points="0,104 620,66 1200,104" fill="#fff"/>
</svg>
<div class="abs arrow-dot" style="left:592px;top:2552px;width:58px;height:58px"><svg width="20" height="24" viewBox="0 0 24 28"><path d="M12 2v22M4 16l8 8 8-8" fill="none" stroke="var(--blue)" stroke-width="2"/></svg></div>

<!-- cause the outcome matters -->
<h2 class="abs section-title" style="top:2650px">CAUSE THE <em>OUTCOME MATTERS</em></h2>
<div class="abs" style="left:434px;top:2764px;width:1px;height:450px;background:var(--line)"></div>
<div class="abs" style="left:774px;top:2764px;width:1px;height:450px;background:var(--line)"></div>
<div class="abs" style="left:133px;top:3000px;width:932px;height:1px;background:var(--line)"></div>

<div class="abs feature feature-hl" style="left:133px;top:2764px;width:301px;height:236px;border-radius:40px 0 0 0;padding-top:44px">
  <svg width="44" height="44" viewBox="0 0 44 44"><circle cx="22" cy="22" r="9" fill="none" stroke="#fff" stroke-width="2"/><circle cx="22" cy="22" r="18" fill="none" stroke="#fff" stroke-width="1.5" stroke-dasharray="4 4"/></svg>
  <h4 style="margin-top:20px">One company for<br>everyone</h4>
  <p>We are a service provider for<br>doctors and hospitals!</p>
</div>
<div class="abs feature" style="left:460px;top:2764px;width:314px;height:236px;padding-top:30px">
  <svg width="56" height="58" viewBox="0 0 56 58"><circle cx="28" cy="14" r="8" fill="none" stroke="var(--navy)" stroke-width="2"/><circle cx="16" cy="34" r="6" fill="none" stroke="var(--blue)" stroke-width="2"/><circle cx="40" cy="34" r="6" fill="none" stroke="var(--blue)" stroke-width="2"/><path d="M4 56q0-14 12-14t12 14M28 56q0-14 12-14t12 14" fill="none" stroke="var(--navy)" stroke-width="2"/></svg>
  <h4>Experience<br>characterises us</h4>
  <p>Our team has many years of ex-<br>perience in the business field!</p>
</div>
<div class="abs feature" style="left:800px;top:2764px;width:265px;height:236px;padding-top:30px">
  <svg width="50" height="66" viewBox="0 0 50 66"><rect x="4" y="6" width="18" height="26" rx="3" fill="none" stroke="var(--navy)" stroke-width="2"/><path d="M13 32v26M8 42h10M8 50h10" stroke="var(--blue)" stroke-width="2"/><path d="M22 14h12q8 0 8 10v10" fill="none" stroke="var(--navy)" stroke-width="2"/></svg>
  <h4>The product is close<br>to our hearts</h4>
  <p>We repair and sell second hand,<br>flexible endoscopes!</p>
</div>
<div class="abs feature" style="left:133px;top:3000px;width:301px;height:214px;padding-top:30px;padding-left:48px">
  <svg width="44" height="52" viewBox="0 0 44 52"><path d="M22 3l18 7v14q0 16-18 25Q4 40 4 24V10z" fill="none" stroke="var(--navy)" stroke-width="2"/><circle cx="22" cy="25" r="9" fill="none" stroke="var(--blue)" stroke-width="2"/><path d="M18 25l3 3 6-6" fill="none" stroke="var(--blue)" stroke-width="2"/></svg>
  <h4 style="margin-top:20px">Guaranteed service</h4>
  <p>You receive a six-month war-<br>ranty on all repairs!</p>
</div>
<div class="abs feature" style="left:467px;top:3000px;width:307px;height:214px;padding-top:38px">
  <svg width="58" height="54" viewBox="0 0 58 54"><path d="M30 3l4 9 10 1-7 7 2 10-9-5-9 5 2-10-7-7 10-1z" fill="none" stroke="var(--navy)" stroke-width="2"/><path d="M4 40h14l10 4h16q6 0 8-6M4 50h40" fill="none" stroke="var(--blue)" stroke-width="2"/></svg>
  <h4>Quality not quantity</h4>
  <p>Reliability and durability instead<br>of inferior replacements!</p>
</div>
<div class="abs feature" style="left:794px;top:3000px;width:271px;height:214px;padding-top:40px">
  <svg width="52" height="60" viewBox="0 0 52 60"><path d="M22 3l18 7v14q0 16-18 25Q4 40 4 24V10z" fill="none" stroke="var(--navy)" stroke-width="2"/><circle cx="34" cy="42" r="10" fill="none" stroke="var(--blue)" stroke-width="2"/><circle cx="34" cy="42" r="4" fill="none" stroke="var(--blue)" stroke-width="2"/></svg>
  <h4>Services for everyone</h4>
  <p>Our service includes the<br>manufacturers Orvana,<br>Pelix and Fuyon!</p>
</div>

<!-- decision -->
<div class="abs decision"></div>
<h2 class="abs dec-title">LUMAVEX GMBH, YOUR DECISION<br>FOR YOUR FUTURE</h2>
<svg class="abs" style="left:420px;top:3490px" width="362" height="362" viewBox="0 0 362 362" aria-hidden="true">
  <circle cx="181" cy="181" r="170" fill="none" stroke="#3a5b76" stroke-width="1.5"/>
  <circle cx="181" cy="181" r="150" fill="none" stroke="var(--blue)" stroke-width="2"/>
</svg>
<div class="abs dec-core"><div class="brand" style="font-size:26px"><span class="brand-dot"></span>Lumavex</div></div>

<div class="abs dec-item dec-left" style="left:180px;top:3532px;width:228px"><b>Fast Repairs</b>Keep potential disruptions in your doctor's office or in your hospital at minimum</div>
<div class="abs dec-icon" style="left:424px;top:3525px"><svg width="28" height="28" viewBox="0 0 28 28"><path d="M4 24L24 4M4 4l20 20" stroke="#fff" stroke-width="2"/></svg></div>
<div class="abs dec-item dec-left" style="left:140px;top:3648px;width:218px"><b>On-site service</b>We will gladly pay you a visit to carry out analysis and repairs on site. Due to our many years of experience</div>
<div class="abs dec-icon" style="left:380px;top:3638px"><svg width="28" height="28" viewBox="0 0 28 28"><circle cx="14" cy="14" r="9" fill="none" stroke="#fff" stroke-width="2"/><circle cx="14" cy="14" r="3" fill="#fff"/></svg></div>
<div class="abs dec-item dec-left" style="left:150px;top:3778px;width:244px"><b>Without a maintenance contract</b>No subscription or other maintenance contract, but one-time and sustainable repair work</div>
<div class="abs dec-icon" style="left:410px;top:3770px"><svg width="28" height="28" viewBox="0 0 28 28"><rect x="4" y="5" width="20" height="14" fill="none" stroke="#fff" stroke-width="2"/><path d="M10 24h8" stroke="#fff" stroke-width="2"/></svg></div>

<div class="abs dec-icon" style="left:706px;top:3525px"><svg width="28" height="28" viewBox="0 0 28 28"><circle cx="14" cy="14" r="10" fill="none" stroke="#fff" stroke-width="2"/><path d="M14 7v14M10 11h6a2 2 0 010 4h-4a2 2 0 000 4h6" fill="none" stroke="#fff" stroke-width="1.5"/></svg></div>
<div class="abs dec-item" style="left:786px;top:3525px;width:240px"><b>Highly cost efficient</b>Benefit from our first class recommendations and implementation by our experienced staff.</div>
<div class="abs dec-icon" style="left:752px;top:3638px"><svg width="28" height="28" viewBox="0 0 28 28"><path d="M4 20h20M8 20V10h12v10" fill="none" stroke="#fff" stroke-width="2"/></svg></div>
<div class="abs dec-item" style="left:826px;top:3638px;width:230px"><b>Loan equipment service</b>We will gladly pay you a visit to carry out analysis and repairs on site. Due to our many years of experience</div>
<div class="abs dec-icon" style="left:712px;top:3770px"><svg width="30" height="28" viewBox="0 0 30 28"><path d="M15 4l3 6 6 1-4 4 1 6-6-3-6 3 1-6-4-4 6-1z" fill="none" stroke="#fff" stroke-width="2"/></svg></div>
<div class="abs dec-item" style="left:786px;top:3778px;width:220px"><b>First class service</b>Our clients always come first!</div>
<a class="abs btn btn-blue dec-btn" href="#">Learn more about Lumavex</a>

<!-- help -->
<div class="abs help"></div>
<h2 class="abs section-title" style="top:4062px;font-size:30px">HOW CAN WE HELP YOU?</h2>
<p class="abs lead" style="top:4128px;left:290px;width:620px;font-size:13.5px;line-height:19px">Lorem ipsum dolor sit amet, consectetur adipiscing elit, sed do eiusmod tempor incididunt ut labore et dolore magna aliqua. Ut enim ad minim veniam, quis nostrud</p>
<div class="abs field" style="left:209px;top:4207px;width:399px;height:50px">
  <svg width="14" height="14" viewBox="0 0 14 14"><circle cx="7" cy="4" r="3" fill="#9aa8b5"/><path d="M1 14q0-6 6-6t6 6z" fill="#9aa8b5"/></svg>First name</div>
<div class="abs field" style="left:209px;top:4261px;width:399px;height:50px">
  <svg width="14" height="14" viewBox="0 0 14 14"><path d="M2 1l3 0 1 3-2 1q1 3 4 4l1-2 3 1 0 3q-9 0-10-10z" fill="#9aa8b5"/></svg>Phone number</div>
<div class="abs field" style="left:209px;top:4315px;width:399px;height:50px">
  <svg width="14" height="12" viewBox="0 0 14 12"><rect x="1" y="1" width="12" height="10" fill="none" stroke="#9aa8b5" stroke-width="1.5"/><path d="M1 1l6 5 6-5" fill="none" stroke="#9aa8b5" stroke-width="1.5"/></svg>Email address</div>
<div class="abs field" style="left:616px;top:4207px;width:396px;height:158px;align-items:flex-start;padding-top:16px">Comments</div>
<a class="abs btn btn-navy submit" href="#">SUBMIT NOW</a>

<svg class="abs" style="left:0;top:4456px" width="1200" height="112" viewBox="0 0 1200 112" aria-hidden="true">
  <polygon points="0,0 610,60 610,112 0,112" fill="var(--blue)"/>
  <polygon points="1200,0 610,60 610,112 1200,112" fill="var(--navy)"/>
  <polygon points="0,112 610,64 1200,112" fill="#fff"/>
</svg>
<div class="abs arrow-dot" style="left:580px;top:4488px;width:60px;height:60px"><svg width="20" height="24" viewBox="0 0 24 28"><path d="M12 26V4M4 12l8-8 8 8" fill="none" stroke="var(--blue)" stroke-width="2"/></svg></div>

<!-- footer -->
<div class="abs brand" style="left:126px;top:4628px;font-size:26px"><span class="brand-dot"></span>Lumavex</div>
<p class="abs" style="left:126px;top:4706px;width:270px;font-size:12.5px;line-height:16px;color:var(--text)">Lorem ipsum dolor sit amet, consectetur adipiscing elit, sed do eiusmod tempor incididunt ut labore et dolore</p>
<div class="abs" style="left:466px;top:4600px;width:1px;height:170px;background:var(--line)"></div>
<div class="abs footer-col" style="left:466px;top:4600px;height:170px">
  <h5>NAVIGATION</h5>
  <ul><li>Home</li><li>Endoscope Repair</li><li>Used Endoscope</li><li>Endoscopy Systems</li></ul>
</div>
<div class="abs footer-col" style="left:702px;top:4600px;height:170px">
  <h5>RESOURCES</h5>
  <ul><li>Endoscopy Accesories</li><li>Purchase</li><li>Contact Us</li></ul>
</div>
<div class="abs footer-col" style="left:912px;top:4600px;height:120px">
  <h5>FOLLOW US</h5>
  <div class="social"><span></span><span></span><span></span><span></span></div>
</div>
<div class="abs copy-line"></div>
<div class="abs copyright">© 2022 Lumavex GmbH</div>

</body>
</html>
```